Business Card Design for Marketing Firm

Looking for business card design for higher end marketing firm. Clean but impressionable/trendy. We are a marketing firm that represents manufacturers in the foodservice equipment and supply industry. Our customers are end users such has hotels, restaurants, country clubs, convention centers and casinos as well as distributors of restaurants supplies and equipment, and manufacturers of foodservice equipment and supplies.
Target Market(s)
Hotels, Restaurants, Supply & Equipment Distributors, Foodservice Manufacturers
Industry/Entity Type
Foodservice/Hospitality
Contact Information for Business Card
Name, Title, Contact Number, Email, Website, Social Media, Address
Requirements
Must have
- Clean & Simple but Serious and Impressionable

```html
<!DOCTYPE html>
<html lang="en">
<head>
<meta charset="utf-8">
<title>Kestrel Supply Partners – Business Card</title>
<link href="https://fonts.googleapis.com/css2?family=Cinzel:wght@700&family=Arimo:wght@400&display=swap" rel="stylesheet">
<style>
  :root {
    --navy: #0b0a7a;
    --white: #ffffff;
    --paper: #e9eaee;
    --card-w: 540px;
    --card-h: 309px;
  }
  * { box-sizing: border-box; margin: 0; padding: 0; }
  html, body { width: 1200px; height: 768px; overflow: hidden; }
  body {
    background: var(--paper);
    display: flex;
    align-items: center;
    justify-content: center;
    gap: 40px;
  }
  .card {
    position: relative;
    width: var(--card-w);
    height: var(--card-h);
    border-radius: 18px;
    overflow: hidden;
    box-shadow: 0 10px 24px rgba(0,0,0,0.18);
  }
  .card-back {
    background: var(--navy);
    display: flex;
    align-items: center;
    justify-content: center;
  }
  .back-name {
    font-family: "Arimo", sans-serif;
    font-weight: 400;
    color: var(--white);
    font-size: 26px;
    letter-spacing: 3px;
    white-space: nowrap;
  }
  .card-front { background: var(--white); }
  .front-wave {
    position: absolute;
    inset: 0;
    width: 100%;
    height: 100%;
  }
  .social-links {
    position: absolute;
    top: 18px;
    left: 20px;
    display: flex;
    gap: 5px;
  }
  .social-dot {
    width: 15px;
    height: 15px;
    border-radius: 50%;
    background: var(--navy);
  }
  .brand-name {
    position: absolute;
    top: 78px;
    left: 0;
    right: 0;
    text-align: center;
    font-family: "Arimo", sans-serif;
    font-weight: 400;
    color: var(--navy);
    font-size: 20px;
    letter-spacing: 2.5px;
    white-space: nowrap;
  }
  .contact-block {
    position: absolute;
    left: 34px;
    top: 198px;
    color: var(--white);
    font-family: "Arimo", sans-serif;
    font-size: 13px;
    white-space: nowrap;
  }
  .person-name {
    font-family: "Cinzel", serif;
    font-weight: 700;
    font-size: 20px;
    letter-spacing: 1px;
    margin-left: 50px;
  }
  .person-title {
    font-family: "Arimo", sans-serif;
    font-weight: 400;
    font-size: 13px;
    letter-spacing: 0;
  }
  .address { margin-top: 6px; margin-left: 24px; }
  .contact-line { margin-top: 6px; }
</style>
</head>
<body>
  <div class="card card-back">
    <div class="back-name">KESTREL SUPPLY PARTNERS</div>
  </div>

  <div class="card card-front">
    <svg class="front-wave" viewBox="0 0 540 309" preserveAspectRatio="none" aria-hidden="true">
      <path d="M0,128 C170,196 400,160 540,224" fill="none" stroke="var(--navy)" stroke-width="2"/>
      <path d="M0,140 C170,206 400,172 540,236 L540,309 L0,309 Z" fill="var(--navy)"/>
    </svg>

    <div class="social-links">
      <span class="social-dot"></span>
      <span class="social-dot"></span>
      <span class="social-dot"></span>
    </div>

    <div class="brand-name">KESTREL SUPPLY PARTNERS</div>

    <div class="contact-block">
      <div class="person-name">NATHAN BROOKS <span class="person-title">/ President</span></div>
      <div class="address">2417 Linden Avenue, Maple Grove, NY 11020</div>
      <div class="contact-line">(555) 0142-7731 &nbsp;|&nbsp; name@KESTREL.com &nbsp;|&nbsp; www.KESTREL.com</div>
    </div>
  </div>
</body>
</html>
```